Schriftdesign für Shop-Header Bild (Schmuckhandel) / Online-Marketing Material
Wir verkaufen Schmuck im Onlineshop mit Herz
Wir benötigen den vorgegebenen Text in schöner Form, Farbe und Größe harmonisch eingefügt, in unserem Bild.
Folgender Text soll sich schick ins Bild einfügen oder in 3-D vielleicht in Schriftfarbe gold hervorheben:
Mit ganzem Herzen für Sie da!
Ihr Online -Juwelier mit Herz
Siehe auch unser altes Bild mit Text, im Shop, wie es nicht aussehen sollte: www.sonnenflocke.de

```html
<!DOCTYPE html>
<html lang="de">
<head>
<meta charset="utf-8">
<title>Header-Schriftvarianten – Mit ganzem Herzen</title>
<link href="https://fonts.googleapis.com/css2?family=Playfair+Display:wght@600;800&family=Cormorant+Garamond:wght@500&family=Gochi+Hand&family=Pinyon+Script&family=Montserrat:wght@700&family=Caveat:wght@500&family=Righteous&family=Inter:wght@300;400;800&display=swap" rel="stylesheet">
<style>
  :root {
    --page: #ffffff;
    --gold: #c2a272;
    --gold-soft: #cdb084;
    --ink: #1a1a1a;
    --satin-light: #f7f3ee;
    --satin-mid: #ece3d8;
    --satin-shadow: #d9cbb9;
    --pendant: #d9b56e;
  }
  * { margin: 0; padding: 0; box-sizing: border-box; }
  html, body { width: 1186px; height: 1200px; overflow: hidden; background: var(--page); }
  .sheet { position: relative; width: 1186px; height: 1200px; }
  .variant { position: absolute; width: 483px; }
  .col-a { left: 74px; }
  .col-b { left: 629px; }
  .row-1 { top: 64px; } .row-2 { top: 252px; } .row-3 { top: 441px; }
  .row-4 { top: 629px; } .row-5 { top: 818px; } .row-6 { top: 1006px; }
  .banner { position: relative; width: 483px; height: 130px; overflow: hidden; }
  .banner-photo {
    position: absolute; inset: 0;
    background:
      radial-gradient(ellipse 70px 80px at 272px 62px, rgba(217,181,110,.85), rgba(217,181,110,0) 100%),
      linear-gradient(160deg, var(--satin-mid) 0%, var(--satin-light) 35%, var(--satin-shadow) 60%, var(--satin-light) 85%, var(--satin-mid) 100%);
  }
  .claim { position: absolute; left: 17px; color: var(--gold); white-space: nowrap; }
  .claim p { display: block; }
  .label { position: absolute; top: 140px; left: 0; font: 800 15px/1 "Inter", sans-serif; color: var(--ink); }

  .serif-condensed { top: 47px; font: 600 15.5px/1.2 "Playfair Display", serif; letter-spacing: -.6px; }
  .stack { top: 41px; left: 16px; }
  .stack .head { font: 600 20px/.95 "Playfair Display", serif; letter-spacing: -.5px; }
  .stack .head.heavy { font-weight: 800; font-size: 21px; letter-spacing: 0; }
  .stack .head.retro { font: 400 16px/1.05 "Righteous", sans-serif; letter-spacing: .3px; }
  .stack .sub { font: 300 9.5px/1.3 "Inter", sans-serif; letter-spacing: -.3px; }
  .stack .sub.dark { color: var(--ink); font-weight: 400; }
  .stack .sub.hand { color: var(--ink); font: 400 10px/1.4 "Gochi Hand", cursive; letter-spacing: .5px; }
  .handwritten { top: 34px; left: 35px; font: 400 17px/.9 "Gochi Hand", cursive; }
  .script { top: 48px; font: 400 16px/1.05 "Pinyon Script", cursive; font-weight: 700; }
  .sans-bold { top: 52px; left: 20px; font: 700 10.5px/1.2 "Montserrat", sans-serif; color: var(--gold-soft); }
  .classic { top: 51px; left: 20px; font: 500 13px/1.2 "Cormorant Garamond", serif; color: var(--gold-soft); }
  .marker { top: 50px; left: 16px; font: 500 16px/1.1 "Caveat", cursive; }
</style>
</head>
<body>
<main class="sheet">

  <section class="variant col-a row-1">
    <div class="banner">
      <div class="banner-photo" role="img" aria-label="Goldener Herzanhänger an feiner Kette auf cremefarbenem Satin"></div>
      <div class="claim serif-condensed"><p>Mit ganzem Herzen für Sie da!</p><p>Ihr Online -Juwelier mit Herz</p></div>
    </div>
    <span class="label">01</span>
  </section>

  <section class="variant col-b row-1">
    <div class="banner">
      <div class="banner-photo" role="img" aria-label="Goldener Herzanhänger an feiner Kette auf cremefarbenem Satin"></div>
      <div class="claim stack"><p class="head">Mit ganzem<br>Herzen für Sie da!</p><p class="sub">Ihr Online -Juwelier mit Herz</p></div>
    </div>
    <span class="label">02</span>
  </section>

  <section class="variant col-a row-2">
    <div class="banner">
      <div class="banner-photo" role="img" aria-label="Goldener Herzanhänger an feiner Kette auf cremefarbenem Satin"></div>
      <div class="claim handwritten"><p>Mit ganzem</p><p>Herzen für Sie da!</p><p>Ihr Online -Juwelier</p><p>mit Herz</p></div>
    </div>
    <span class="label">03</span>
  </section>

  <section class="variant col-b row-2">
    <div class="banner">
      <div class="banner-photo" role="img" aria-label="Goldener Herzanhänger an feiner Kette auf cremefarbenem Satin"></div>
      <div class="claim stack"><p class="head heavy">Mit ganzem<br>Herzen fur Sie da!</p><p class="sub">Ihr Online -Juwelier mit Herz</p></div>
    </div>
    <span class="label">04</span>
  </section>

  <section class="variant col-a row-3">
    <div class="banner">
      <div class="banner-photo" role="img" aria-label="Goldener Herzanhänger an feiner Kette auf cremefarbenem Satin"></div>
      <div class="claim script"><p>Mit ganzem Herzen für Sie da!</p><p>Ihr Online -Juwelier mit Herz</p></div>
    </div>
    <span class="label">05</span>
  </section>

  <section class="variant col-b row-3">
    <div class="banner">
      <div class="banner-photo" role="img" aria-label="Goldener Herzanhänger an feiner Kette auf cremefarbenem Satin"></div>
      <div class="claim stack"><p class="head">Mit ganzem<br>Herzen für Sie da!</p><p class="sub dark">Ihr Online -Juwelier mit Herz</p></div>
    </div>
    <span class="label">06</span>
  </section>

  <section class="variant col-a row-4">
    <div class="banner">
      <div class="banner-photo" role="img" aria-label="Goldener Herzanhänger an feiner Kette auf cremefarbenem Satin"></div>
      <div class="claim sans-bold"><p>Mit ganzem Herzen für Sie da!</p><p>Ihr Online -Juwelier mit Herz</p></div>
    </div>
    <span class="label">07</span>
  </section>

  <section class="variant col-b row-4">
    <div class="banner">
      <div class="banner-photo" role="img" aria-label="Goldener Herzanhänger an feiner Kette auf cremefarbenem Satin"></div>
      <div class="claim stack"><p class="head heavy">Mit ganzem<br>Herzen fur Sie da!</p><p class="sub dark">Ihr Online -Juwelier mit Herz</p></div>
    </div>
    <span class="label">08</span>
  </section>

  <section class="variant col-a row-5">
    <div class="banner">
      <div class="banner-photo" role="img" aria-label="Goldener Herzanhänger an feiner Kette auf cremefarbenem Satin"></div>
      <div class="claim classic"><p>Mit ganzem Herzen fur Sie da!</p><p>Ihr Online -Juwelier mit Herz</p></div>
    </div>
    <span class="label">09</span>
  </section>

  <section class="variant col-b row-5">
    <div class="banner">
      <div class="banner-photo" role="img" aria-label="Goldener Herzanhänger an feiner Kette auf cremefarbenem Satin"></div>
      <div class="claim stack"><p class="head heavy">Mit ganzem<br>Herzen fur Sie da!</p><p class="sub hand">Ihr Online -Juwelier mit Herz</p></div>
    </div>
    <span class="label">10</span>
  </section>

  <section class="variant col-a row-6">
    <div class="banner">
      <div class="banner-photo" role="img" aria-label="Goldener Herzanhänger an feiner Kette auf cremefarbenem Satin"></div>
      <div class="claim marker"><p>Mit ganzem Herzen für Sie da!</p><p>Ihr Online -Juwelier mit Herz</p></div>
    </div>
    <span class="label">11</span>
  </section>

  <section class="variant col-b row-6">
    <div class="banner">
      <div class="banner-photo" role="img" aria-label="Goldener Herzanhänger an feiner Kette auf cremefarbenem Satin"></div>
      <div class="claim stack"><p class="head retro">Mit ganzem<br>Herzen für Sie da!</p><p class="sub dark">Ihr Online -Juwelier mit Herz</p></div>
    </div>
    <span class="label">12</span>
  </section>

</main>
</body>
</html>
```